Redesign of Medical App for Patients

• The Designer’s task is to provide a new fully-responsive design for our apps, and then code it using only basic html and CSS.
• Your design will be incorporated into our existing REACT native app.

Target Market(s)

Medical Patients

Industry/Entity Type

Medical

Coding

Coded - Design and coding required

Number of Pages Required

5+ page

Requirements
Must have
• Short list candidates will receive detailed briefing
Nice to have
• detailed briefing contains some of our ideas.

```html
<!DOCTYPE html>
<html lang="en">
<head>
<meta charset="UTF-8">
<title>CareGuide – Patient App Screens</title>
<link href="https://fonts.googleapis.com/css2?family=Exo+2:wght@500;600&family=Poppins:wght@400;500;600&display=swap" rel="stylesheet">
<style>
  :root {
    --bg-start: #c6cbee;
    --bg-end: #e6e5fb;
    --sky-light: #aee6fb;
    --sky: #3cc3f5;
    --sky-deep: #16a9ec;
    --tile: #0492d3;
    --ink: #1b1b1b;
    --ink-soft: #3a3a3a;
    --title-blue: #0a8fd4;
    --panel: #efeff1;
    --white: #ffffff;
    --placeholder: rgba(255, 255, 255, 0.32);
  }
  * { box-sizing: border-box; margin: 0; padding: 0; }
  html, body { width: 1200px; height: 710px; overflow: hidden; }
  body {
    background: linear-gradient(160deg, var(--bg-start), var(--bg-end));
    font-family: "Poppins", sans-serif;
    position: relative;
  }
  .screen {
    position: absolute;
    top: 70px;
    width: 254px;
    height: 550px;
    border-radius: 26px;
    overflow: hidden;
    background: var(--white);
    box-shadow: 0 14px 34px rgba(80, 90, 170, 0.28);
  }
  .screen--contents { left: 123px; }
  .screen--about { left: 477px; }
  .screen--article { left: 830px; }

  .hero {
    position: absolute; left: 0; top: 0; width: 100%;
    background: linear-gradient(180deg, var(--sky-light) 0%, var(--sky) 60%, var(--sky-deep) 100%);
  }
  .hero-art { position: absolute; }
  .hero-art--neutral { background: var(--placeholder); border-radius: 12px; }
  .curve { position: absolute; left: 0; width: 254px; display: block; }

  .status-bar {
    position: absolute; top: 9px; left: 0; width: 100%;
    display: flex; justify-content: space-between; align-items: center;
    padding: 0 12px 0 24px;
    font-size: 10px; color: var(--white);
    z-index: 3;
  }
  .status-icons { display: flex; gap: 4px; align-items: center; }

  .app-header {
    position: absolute; top: 26px; left: 0; width: 100%;
    display: flex; justify-content: space-between; align-items: center;
    padding: 0 12px;
    z-index: 3;
  }
  .brand { display: flex; align-items: center; gap: 5px; }
  .brand-dot { width: 16px; height: 16px; border-radius: 50%; background: var(--tile); }
  .brand-name { font-size: 11px; font-weight: 500; color: #0a6fa8; letter-spacing: 0.2px; }

  .section-title {
    position: absolute; left: 0; width: 100%;
    text-align: center; font-size: 13px; font-weight: 500; color: var(--ink);
  }

  .toc { position: absolute; left: 10px; top: 247px; width: 233px; list-style: none; }
  .toc-item {
    height: 43px; margin-bottom: 7px;
    background: var(--tile); border-radius: 5px;
    display: flex; align-items: center; padding: 0 12px;
    color: var(--white);
  }
  .toc-icon { width: 26px; height: 26px; flex: none; }
  .toc-text { flex: 1; text-align: center; font-family: "Exo 2", sans-serif; line-height: 1.15; }
  .toc-title { font-size: 14px; font-weight: 500; display: block; }
  .toc-sub { font-size: 9px; display: block; }
  .chevron { width: 8px; height: 12px; flex: none; }

  .tiles {
    position: absolute; left: 10px; top: 310px; width: 233px;
    display: grid; grid-template-columns: 113px 113px; gap: 5px 7px;
  }
  .tile {
    height: 81px; background: var(--tile); border-radius: 5px;
    color: var(--white); font-family: "Exo 2", sans-serif; font-size: 11px; line-height: 1.4;
    padding: 0 14px 0 8px; display: flex; align-items: center; position: relative;
  }
  .tile .chevron { position: absolute; right: 8px; bottom: 11px; }

  .pager { position: absolute; top: 487px; right: 14px; display: flex; gap: 10px; }
  .pager-btn {
    width: 31px; height: 31px; border-radius: 50%; background: var(--tile);
    display: flex; align-items: center; justify-content: center;
  }

  .article-title {
    position: absolute; top: 196px; left: 0; width: 100%;
    text-align: center; font-family: "Exo 2", sans-serif; font-weight: 600;
    font-size: 13.5px; line-height: 23px; color: var(--title-blue);
  }
  .article-body {
    position: absolute; top: 255px; left: 10px; width: 232px; height: 222px;
    background: var(--panel); border-radius: 5px;
    padding: 9px 6px; box-shadow: 0 1px 4px rgba(0,0,0,0.12);
  }
  .article-body p {
    font-size: 7.8px; line-height: 12.9px; color: var(--ink-soft);
    text-align: justify; margin-bottom: 4px; letter-spacing: -0.1px;
  }
</style>
</head>
<body>

<section class="screen screen--contents">
  <div class="hero" style="height:240px;">
    <div class="hero-art hero-art--neutral" role="img" aria-label="Smiling doctor in a white coat with a stethoscope" style="left:55px;top:60px;width:150px;height:150px;"></div>
  </div>
  <svg class="curve" style="top:188px;" height="52" viewBox="0 0 254 52"><path d="M0 46 Q127 -44 254 46 V52 H0Z" fill="#fff"/></svg>
  <div class="status-bar"><span>9:30</span><span class="status-icons">
    <svg width="10" height="7"><rect x="0" y="5" width="2" height="2" fill="#fff"/><rect x="3" y="3" width="2" height="4" fill="#fff"/><rect x="6" y="1" width="2" height="6" fill="#fff"/></svg>
    <svg width="15" height="7"><rect x=".5" y=".5" width="12" height="6" rx="1.5" fill="none" stroke="#fff"/><rect x="2" y="2" width="9" height="3" fill="#fff"/></svg></span></div>
  <header class="app-header">
    <svg width="16" height="12"><path d="M1 1h14M1 6h10M1 11h14" stroke="#1b1b1b" stroke-width="1.6" stroke-linecap="round"/></svg>
    <div class="brand"><span class="brand-dot"></span><span class="brand-name">CAREGUIDE</span></div>
    <svg width="14" height="14" viewBox="0 0 14 14"><circle cx="7" cy="7" r="5" fill="none" stroke="#111" stroke-width="3" stroke-dasharray="2 1.6"/><circle cx="7" cy="7" r="3.2" fill="#111"/><circle cx="7" cy="7" r="1.4" fill="#3cc3f5"/></svg>
  </header>
  <h2 class="section-title" style="top:214px;">Table Of Contents</h2>
  <ul class="toc">
    <li class="toc-item">
      <svg class="toc-icon" viewBox="0 0 26 26" fill="none" stroke="#fff" stroke-width="1.3"><circle cx="5" cy="6" r="3"/><rect x="9" y="4" width="14" height="4" rx="2"/><rect x="3" y="14" width="14" height="4" rx="2"/><circle cx="21" cy="16" r="3"/><path d="M19.5 16l1 1 2-2"/></svg>
      <span class="toc-text"><span class="toc-title">About Procedure</span><span class="toc-sub">Why and how is it done</span></span>
      <svg class="chevron" viewBox="0 0 8 12"><path d="M2 1l5 5-5 5" stroke="#fff" stroke-width="1.6" fill="none"/></svg>
    </li>
    <li class="toc-item">
      <svg class="toc-icon" viewBox="0 0 26 26" fill="none" stroke="#fff" stroke-width="1.3"><circle cx="13" cy="6" r="3"/><path d="M8 13c0-3 10-3 10 0"/><rect x="3" y="15" width="7" height="9"/><circle cx="20" cy="19" r="4"/></svg>
      <span class="toc-text"><span class="toc-title">Pre - Procedure</span><span class="toc-sub">How to get ready</span></span>
      <svg class="chevron" viewBox="0 0 8 12"><path d="M2 1l5 5-5 5" stroke="#fff" stroke-width="1.6" fill="none"/></svg>
    </li>
    <li class="toc-item">
      <svg class="toc-icon" viewBox="0 0 26 26" fill="#fff"><rect x="2" y="3" width="7" height="6"/><rect x="9" y="11" width="7" height="6"/><rect x="17" y="19" width="7" height="6"/><path d="M11 5h3v4M18 13h3v4" stroke="#fff" fill="none" stroke-width="1.2"/></svg>
      <span class="toc-text"><span class="toc-title">Procedure</span><span class="toc-sub" style="font-size:7.5px;line-height:1;">The day of procedure - in the<br>operating room</span></span>
      <svg class="chevron" viewBox="0 0 8 12"><path d="M2 1l5 5-5 5" stroke="#fff" stroke-width="1.6" fill="none"/></svg>
    </li>
    <li class="toc-item">
      <svg class="toc-icon" viewBox="0 0 26 26" fill="none" stroke="#fff" stroke-width="1.3"><circle cx="13" cy="13" r="10" stroke-dasharray="40 6"/><circle cx="13" cy="13" r="6"/><path d="M13 10v6M10 13h6"/></svg>
      <span class="toc-text"><span class="toc-title">Recovery</span><span class="toc-sub">Expectations immediately after surgery</span></span>
      <svg class="chevron" viewBox="0 0 8 12"><path d="M2 1l5 5-5 5" stroke="#fff" stroke-width="1.6" fill="none"/></svg>
    </li>
    <li class="toc-item">
      <svg class="toc-icon" viewBox="0 0 26 26" fill="#fff"><path d="M13 3L2 13h3v10h6v-6h4v6h6V13h3z"/></svg>
      <span class="toc-text"><span class="toc-title">At Home</span><span class="toc-sub">How to care for yourself afterwards</span></span>
      <svg class="chevron" viewBox="0 0 8 12"><path d="M2 1l5 5-5 5" stroke="#fff" stroke-width="1.6" fill="none"/></svg>
    </li>
    <li class="toc-item">
      <svg class="toc-icon" viewBox="0 0 26 26" fill="none" stroke="#fff" stroke-width="1.6"><rect x="3" y="6" width="5" height="5"/><path d="M11 8h11M11 18h11M3 18l2 2 3-4"/></svg>
      <span class="toc-text"><span class="toc-title">What to do if</span><span class="toc-sub">Reponding to your issues</span></span>
      <svg class="chevron" viewBox="0 0 8 12"><path d="M2 1l5 5-5 5" stroke="#fff" stroke-width="1.6" fill="none"/></svg>
    </li>
  </ul>
</section>

<section class="screen screen--about">
  <div class="hero" style="height:300px;">
    <div class="hero-art hero-art--neutral" role="img" aria-label="Anatomical illustration of the liver, gallbladder and pancreas" style="left:42px;top:78px;width:180px;height:150px;"></div>
  </div>
  <svg class="curve" style="top:252px;" height="48" viewBox="0 0 254 48"><path d="M0 40 Q127 -38 254 40 V48 H0Z" fill="#fff"/></svg>
  <div class="status-bar"><span>9:30</span><span class="status-icons">
    <svg width="10" height="7"><rect x="0" y="5" width="2" height="2" fill="#fff"/><rect x="3" y="3" width="2" height="4" fill="#fff"/><rect x="6" y="1" width="2" height="6" fill="#fff"/></svg>
    <svg width="15" height="7"><rect x=".5" y=".5" width="12" height="6" rx="1.5" fill="none" stroke="#fff"/><rect x="2" y="2" width="9" height="3" fill="#fff"/></svg></span></div>
  <header class="app-header">
    <svg width="16" height="12"><path d="M15 6H2M6 1L1 6l5 5" stroke="#1b1b1b" stroke-width="1.6" fill="none" stroke-linecap="round"/></svg>
    <div class="brand"><span class="brand-dot"></span><span class="brand-name">CAREGUIDE</span></div>
    <svg width="14" height="14" viewBox="0 0 14 14"><circle cx="7" cy="7" r="5" fill="none" stroke="#111" stroke-width="3" stroke-dasharray="2 1.6"/><circle cx="7" cy="7" r="3.2" fill="#111"/><circle cx="7" cy="7" r="1.4" fill="#3cc3f5"/></svg>
  </header>
  <h2 class="section-title" style="top:277px;">About Procedure</h2>
  <div class="tiles">
    <a class="tile">Is it too late to prevent gallbladder disease?<svg class="chevron" viewBox="0 0 8 12"><path d="M2 1l5 5-5 5" stroke="#fff" stroke-width="1.6" fill="none"/></svg></a>
    <a class="tile">What will happen if I don’t have this procedure?<svg class="chevron" viewBox="0 0 8 12"><path d="M2 1l5 5-5 5" stroke="#fff" stroke-width="1.6" fill="none"/></svg></a>
    <a class="tile">Are there alternative solutions?<svg class="chevron" viewBox="0 0 8 12"><path d="M2 1l5 5-5 5" stroke="#fff" stroke-width="1.6" fill="none"/></svg></a>
    <a class="tile">What are the risks of this procedure?<svg class="chevron" viewBox="0 0 8 12"><path d="M2 1l5 5-5 5" stroke="#fff" stroke-width="1.6" fill="none"/></svg></a>
  </div>
  <nav class="pager">
    <span class="pager-btn"><svg width="8" height="12"><path d="M6 1L1 6l5 5" stroke="#fff" stroke-width="1.8" fill="none"/></svg></span>
    <span class="pager-btn"><svg width="8" height="12"><path d="M2 1l5 5-5 5" stroke="#fff" stroke-width="1.8" fill="none"/></svg></span>
  </nav>
</section>

<section class="screen screen--article">
  <div class="hero" style="height:220px;">
    <div class="hero-art" role="img" aria-label="Patient seated in a clinic room talking with a doctor beside an anatomical model" style="left:0;top:0;width:254px;height:220px;background:linear-gradient(180deg,#bfe6f6 0%,#8fcbe6 45%,#5aa9cf 100%);"></div>
  </div>
  <svg class="curve" style="top:172px;" height="48" viewBox="0 0 254 48"><path d="M0 46 Q127 -44 254 46 V48 H0Z" fill="#fff"/></svg>
  <div class="status-bar"><span>9:30</span><span class="status-icons">
    <svg width="10" height="7"><rect x="0" y="5" width="2" height="2" fill="#fff"/><rect x="3" y="3" width="2" height="4" fill="#fff"/><rect x="6" y="1" width="2" height="6" fill="#fff"/></svg>
    <svg width="15" height="7"><rect x=".5" y=".5" width="12" height="6" rx="1.5" fill="none" stroke="#fff"/><rect x="2" y="2" width="9" height="3" fill="#fff"/></svg></span></div>
  <header class="app-header">
    <svg width="16" height="12"><path d="M15 6H2M6 1L1 6l5 5" stroke="#1b1b1b" stroke-width="1.6" fill="none" stroke-linecap="round"/></svg>
    <div class="brand"><span class="brand-dot"></span><span class="brand-name">CAREGUIDE</span></div>
    <svg width="14" height="14" viewBox="0 0 14 14"><circle cx="7" cy="7" r="5" fill="none" stroke="#111" stroke-width="3" stroke-dasharray="2 1.6"/><circle cx="7" cy="7" r="3.2" fill="#111"/><circle cx="7" cy="7" r="1.4" fill="#3cc3f5"/></svg>
  </header>
  <h1 class="article-title">Is it too late to prevent<br>gallbladder disease?</h1>
  <article class="article-body">
    <p>Yes, unfortunately. If you have symptomatic gallbladder disease, surgery is the most likely solution. Gallstones rarely go away spontaneously.</p>
    <p>It is not entirely understood why some people get gallstones. Probable factors include weight, level of physical activity, pregnancy, certain medications containing estrogen, and diet. For example, sometimes patients will try to decrease the amount of fat they consume to avoid gallbladder attacks.</p>
    <p>There are numerous homeopathic/natural remedies that suggest they can treat gallbladder disease on their own, but these have not been proven scientifically. There are other more proven solutions to eliminate gallstones – if only temporarily – as well as another surgery to do the same. See below.</p>
  </article>
  <nav class="pager">
    <span class="pager-btn"><svg width="8" height="12"><path d="M6 1L1 6l5 5" stroke="#fff" stroke-width="1.8" fill="none"/></svg></span>
    <span class="pager-btn"><svg width="8" height="12"><path d="M2 1l5 5-5 5" stroke="#fff" stroke-width="1.8" fill="none"/></svg></span>
  </nav>
</section>

</body>
</html>
```